Hello Creative Minds!
Our business is after a elegant and classy flyer that draws attention!
The business is Velvet Turf - Lawn Revival Services. We provide services that maintain a healthy and vibrant green lawn through the tough Australian seasons. The products we use limits the water needed to keep grass green to a minimum - practically none at all! This not only helps the home owner or home seller but the environment by limiting the use of water that is needed to create a green lawn. The products we use are made from natural ingredients that are and pet friendly.
This fly will be our introductory offer to the market. Below are the required points that need to be on the flyer. Attached is the business logo, before & after pictures and 1 example of the LAYOUT not DESIGN of what the flyer should be laid out like or similar to. Feel free to use different 'Lawn Mower' pictures.
All the best; if you need any questions answered please feel free to message.
REQUIRED POINTS (Please re-phrase were possible);
*Instantly restores the natural green colour of grass – year round
*Lasts for up to 3 months
*Substantially reduces watering needs
*Pet friendly
*Stays green during droughts and water restrictions
*UV fade resistant
*Won’t bleed, run, or stain once absorbed into the grass
*Safe for the environment, pets and people
*Works in extreme heat, cold and frost
*Organic and natural – no harmful chemicals
*Reduces the amount of fertilizer
and water used on lawns
*Kerb appeal is essential for getting your property sold for the highest price possible
SERVICES & PRICING
Lawn maintenance (cut & trim) starting from $60
Lawn rejuvenation starting from $80 (Only $27 a month for 3 months)*
Package deal starting from $120
Introductory offer: 25% off all services. Refer a friend, when they book you receive another 25% off your next service.
LOCATIONS
Nowra to Sydney
CONTACT NUMBER
Will be posted with the winner - please leave an area for this.
SOCIAL MEDIA
Please add Chatterbook and Snapgrid logo's
Updates
Target Market(s)
home owners, home sellers, property developers, real estates and nursing homes and government housing.
Industry/Entity Type
Lawn Care
Look and feel
Each slider illustrates characteristics of the customer's brand and the style your logo design should communicate.

```html
<!DOCTYPE html>
<html lang="en">
<head>
<meta charset="utf-8">
<title>Velvet Turf – Lawn Revival Services Flyer</title>
<link rel="stylesheet" href="https://fonts.googleapis.com/css2?family=Montserrat:wght@400;600;700&family=Yellowtail&display=swap">
<style>
  :root {
    --page: #d9d9d7;
    --flyer: #23262f;
    --ink: #ffffff;
    --muted: #d6d8dc;
    --lime: #c9da3b;
    --green: #86b83a;
    --deep-green: #5d9a2c;
    --yellow: #f6cf05;
    --frame: #e9ecef;
  }
  * { box-sizing: border-box; margin: 0; padding: 0; }
  html, body { width: 1200px; height: 860px; overflow: hidden; }
  body { background: var(--page); font-family: "Montserrat", sans-serif; color: var(--ink); }

  .flyer {
    position: absolute; left: 310px; top: 20px;
    width: 580px; height: 820px;
    background: var(--flyer);
    box-shadow: 0 6px 18px rgba(0,0,0,.25);
    overflow: hidden;
  }

  .headline {
    position: absolute; left: 34px; top: 30px; z-index: 4;
    font-family: "Yellowtail", cursive; font-weight: 400;
    font-size: 72px; line-height: 68px;
    background: linear-gradient(90deg, var(--lime), var(--green));
    -webkit-background-clip: text; background-clip: text; color: transparent;
    filter: drop-shadow(2px 3px 2px rgba(0,0,0,.55));
    white-space: nowrap;
  }
  .headline span { display: block; }
  .headline .line-two { padding-left: 165px; }

  .photo-frame {
    position: absolute; left: 118px; top: 134px;
    width: 340px; height: 342px;
    border: 2px solid var(--frame); padding: 6px;
  }
  .photo {
    width: 100%; height: 158px;
    background: linear-gradient(180deg, #6f7a76 0%, #7b8581 38%, #83b14c 42%, #6aa23a 62%, #5b5f63 66%, #4d5155 100%);
  }
  .photo + .photo { margin-top: 10px; }
  .photo-before { filter: saturate(.8) brightness(.95); }

  .overlay { position: absolute; left: 0; top: 0; z-index: 3; }

  .offer {
    position: absolute; left: 36px; top: 280px; z-index: 5;
    width: 196px; padding: 7px 6px 6px;
    background: var(--yellow); color: #1c1c1c; text-align: center;
    transform: rotate(-2deg);
    border: 1px solid #fff6b0;
  }
  .offer-title { font-weight: 700; font-size: 12.5px; line-height: 14px; }
  .offer-note { font-weight: 700; font-size: 7.6px; line-height: 10px; margin-top: 4px; }

  .boxed { position: absolute; border: 1px solid var(--frame); }
  .boxed-title {
    position: absolute; top: -8px; left: 50%; transform: translateX(-50%);
    background: var(--flyer); padding: 0 4px;
    font-weight: 700; font-size: 11px; letter-spacing: .3px; white-space: nowrap;
  }

  .benefits { left: 40px; top: 510px; width: 328px; height: 174px; padding: 16px 8px 6px 10px; display: flex; gap: 8px; }
  .benefit-list { list-style: none; flex: 1; }
  .benefit-list li {
    position: relative; padding-left: 10px; margin-bottom: 3px;
    font-size: 8px; line-height: 10px; color: var(--muted);
  }
  .benefit-list li::before {
    content: "✓"; position: absolute; left: 0; top: 0;
    color: var(--lime); font-weight: 700;
  }

  .services { left: 384px; top: 502px; width: 168px; height: 160px; padding: 16px 10px 8px 12px; }
  .service { margin-bottom: 8px; }
  .service-name { color: var(--lime); font-weight: 700; font-size: 9.6px; letter-spacing: .3px; text-transform: uppercase; }
  .service-price { font-size: 8.3px; color: var(--muted); }
  .service-price strong { font-size: 12px; color: var(--ink); }

  .brand {
    position: absolute; left: 120px; top: 696px; width: 250px; text-align: center;
    color: var(--green);
  }
  .brand-name { font-weight: 700; font-size: 32px; line-height: 36px; letter-spacing: .5px; }
  .brand-tagline { font-weight: 700; font-size: 8px; letter-spacing: 3px; text-transform: uppercase; }

  .call {
    position: absolute; left: 60px; top: 774px;
    font-weight: 700; font-size: 17px; letter-spacing: .5px; white-space: nowrap;
  }
  .call .phone { color: var(--green); font-size: 25px; margin-left: 6px; letter-spacing: 1px; }

  .contacts { position: absolute; left: 420px; top: 696px; list-style: none; }
  .contacts li { display: flex; align-items: center; gap: 8px; height: 24px; margin-bottom: 6px; font-size: 8.5px; color: var(--muted); }
  .contact-icon { width: 22px; height: 22px; background: var(--lime); display: flex; align-items: center; justify-content: center; }
</style>
</head>
<body>
<main class="flyer">

  <h1 class="headline"><span class="line-one">Make your lawn</span><span class="line-two">great again!</span></h1>

  <div class="photo-frame">
    <div class="photo photo-before" role="img" aria-label="Backyard lawn before treatment, patchy grass beside a paved patio"></div>
    <div class="photo photo-after" role="img" aria-label="The same backyard after treatment, lush green lawn beside a paved patio"></div>
  </div>

  <svg class="overlay" width="580" height="820" viewBox="0 0 580 820">
    <defs>
      <radialGradient id="dry-grass" cx="50%" cy="45%" r="60%">
        <stop offset="0%" stop-color="#b89a6a"/>
        <stop offset="100%" stop-color="#7d6543"/>
      </radialGradient>
      <radialGradient id="fresh-grass" cx="50%" cy="45%" r="60%">
        <stop offset="0%" stop-color="#7fb548"/>
        <stop offset="100%" stop-color="#3f7a26"/>
      </radialGradient>
      <path id="before-arc" d="M 52 215 A 70 70 0 0 1 96 122"/>
      <path id="after-arc" d="M 470 235 A 76 76 0 0 1 513 317"/>
    </defs>
    <g role="img" aria-label="Close-up of dry, straw-coloured grass">
      <circle cx="120" cy="188" r="60" fill="url(#dry-grass)" stroke="#ffffff" stroke-width="2"/>
    </g>
    <g role="img" aria-label="Close-up of lush green grass">
      <circle cx="438" cy="304" r="63" fill="url(#fresh-grass)" stroke="#ffffff" stroke-width="2"/>
    </g>
    <text font-family="Montserrat, sans-serif" font-weight="700" font-size="11" letter-spacing="4" fill="#ffffff">
      <textPath href="#before-arc">BEFORE</textPath>
    </text>
    <text font-family="Montserrat, sans-serif" font-weight="700" font-size="11" letter-spacing="4" fill="#ffffff">
      <textPath href="#after-arc">AFTER</textPath>
    </text>
  </svg>

  <aside class="offer">
    <p class="offer-title">INTRODUCTORY OFFER:<br>25% OFF ALL SERVICES</p>
    <p class="offer-note">Refer a friend: When they book, you will receive 25% off your next service!</p>
  </aside>

  <section class="boxed benefits">
    <h2 class="boxed-title">DIRECT BENEFITS</h2>
    <ul class="benefit-list">
      <li>Instantly restores the natural green colour of grass – year round</li>
      <li>Lasts for up to 3 months</li>
      <li>Substantially reduces watering needs</li>
      <li>Pet friendly</li>
      <li>Stays green during droughts and water restrictions</li>
      <li>UV fade resistant</li>
      <li>Won’t bleed, run, or stain once absorbed into the grass</li>
    </ul>
    <ul class="benefit-list">
      <li>Safe for the environment, pets and people</li>
      <li>Works in extreme heat, cold and frost</li>
      <li>Organic and natural – no harmful chemicals</li>
      <li>Reduces the amount of fertilizer and water used on lawns</li>
      <li>Kerb appeal is essential for getting your property sold for the highest price</li>
    </ul>
  </section>

  <section class="boxed services">
    <h2 class="boxed-title">SERVICES &amp; PRICING</h2>
    <div class="service"><p class="service-name">Lawn Maintenance</p><p class="service-price">Starting from <strong>$60</strong></p></div>
    <div class="service"><p class="service-name">Lawn Rejuvenation</p><p class="service-price">Starting from <strong>$80</strong></p></div>
    <div class="service"><p class="service-name">Package Deal</p><p class="service-price">Starting from <strong>$120</strong></p></div>
    <div class="service"><p class="service-name">Locations</p><p class="service-price">Nowra to Sydney</p></div>
  </section>

  <div class="brand">
    <p class="brand-name">Velvet Turf</p>
    <p class="brand-tagline">Lawn Revival Services</p>
  </div>

  <p class="call">CALL US TODAY <span class="phone">02 5550 1234</span></p>

  <ul class="contacts">
    <li>
      <span class="contact-icon">
        <svg width="14" height="10" viewBox="0 0 14 10" aria-label="Email"><rect x="0.75" y="0.75" width="12.5" height="8.5" fill="none" stroke="#23262f" stroke-width="1.5"/><path d="M1 1 L7 6 L13 1" fill="none" stroke="#23262f" stroke-width="1.5"/></svg>
      </span>
      hello@velvetturf.example
    </li>
    <li><span class="contact-icon" aria-label="Chatterbook"></span>@velvetturfau</li>
    <li><span class="contact-icon" aria-label="Snapgrid"></span>@velvetturfau</li>
  </ul>

</main>
</body>
</html>
```